We are a recruitment company based in Norwich/Cambridge England.
I have included our company logo which we want to remain the same.

What we are looking for is a new creative Business card which will really stand out!!

Contact Information for Business Card

Harriet Dunmore
email: Harriet@plavex.co.uk
Address: Brackwell House
Fenmoor Enterprise Park
Partridge Way
Norwich
QB9 3KX
Tel:01632 960418

```html
<!DOCTYPE html>
<html lang="en">
<head>
<meta charset="utf-8">
<title>Plavex Business Card</title>
<link rel="stylesheet" href="https://fonts.googleapis.com/css2?family=Roboto:wght@400;500&family=Roboto+Condensed:wght@500&display=swap">
<style>
  :root {
    --backdrop: #2b2b2b;
    --card-white: #f1f1f1;
    --brand-green: #8dc540;
    --text-grey: #555555;
    --logo-grey: #8a8a8c;
    --white: #ffffff;
  }
  html, body {
    margin: 0;
    padding: 0;
    width: 1200px;
    height: 960px;
    overflow: hidden;
    background: var(--backdrop);
    font-family: "Roboto", Arial, sans-serif;
  }
  .stage { position: relative; width: 1200px; height: 960px; }
  .card {
    position: absolute;
    width: 600px;
    height: 342px;
    box-sizing: border-box;
  }
  .card-front { left: 322px; top: 108px; background: var(--card-white); }
  .card-back { left: 320px; top: 493px; background: var(--brand-green); }

  .name-band {
    position: absolute;
    left: 0; top: 36px;
    width: 330px; height: 67px;
    background: var(--brand-green);
    color: var(--white);
  }
  .name-band .person-name {
    position: absolute; left: 30px; top: 12px;
    font-family: "Roboto Condensed", Arial, sans-serif;
    font-weight: 500; font-size: 21px; letter-spacing: 0.2px;
  }
  .name-band .person-role {
    position: absolute; left: 30px; top: 38px;
    font-family: "Roboto Condensed", Arial, sans-serif;
    font-weight: 500; font-size: 14px;
  }
  .brand-lockup {
    position: absolute; right: 28px; top: 48px;
    display: flex; align-items: center; gap: 10px;
  }
  .brand-mark {
    width: 34px; height: 34px; border-radius: 50%;
    background: var(--brand-green);
  }
  .brand-name {
    font-size: 36px; font-weight: 500; color: var(--logo-grey);
    line-height: 1;
  }

  .contact-list {
    position: absolute; left: 30px; top: 232px;
    margin: 0; padding: 0; list-style: none;
    font-size: 14px; color: var(--text-grey);
  }
  .contact-list li {
    display: flex; align-items: center; gap: 8px;
    height: 19px;
  }
  .contact-list svg { width: 13px; height: 13px; fill: var(--brand-green); }

  .address {
    position: absolute; right: 28px; top: 255px;
    text-align: right; font-size: 14px; color: var(--text-grey);
    line-height: 19px;
  }
  .address .web { letter-spacing: 1.6px; }

  .back-brand {
    position: absolute; left: 0; right: 0; top: 140px;
    display: flex; justify-content: center; align-items: center; gap: 18px;
  }
  .back-brand .brand-mark { width: 60px; height: 60px; background: var(--white); }
  .back-brand .brand-name { font-size: 64px; color: var(--white); }
  .back-web {
    position: absolute; left: 0; right: 0; top: 300px;
    text-align: center; color: var(--white);
    font-size: 14px; letter-spacing: 5px;
  }
</style>
</head>
<body>
<div class="stage">
  <section class="card card-front">
    <div class="name-band">
      <div class="person-name">HARRIET DUNMORE</div>
      <div class="person-role">CEO/FOUNDER</div>
    </div>
    <div class="brand-lockup">
      <span class="brand-mark"></span>
      <span class="brand-name">Plavex</span>
    </div>

    <ul class="contact-list">
      <li>
        <svg viewBox="0 0 16 16" aria-hidden="true"><path d="M3.6 1.2l2.3 2.9-1.4 1.8c.9 2 2.5 3.6 4.5 4.5l1.8-1.4 2.9 2.3-1.5 2.5C7 13.4 2.6 9 1.1 2.7z"/></svg>
        01632 960418
      </li>
      <li>
        <svg viewBox="0 0 16 16" aria-hidden="true"><path d="M4 0h8a1 1 0 0 1 1 1v14a1 1 0 0 1-1 1H4a1 1 0 0 1-1-1V1a1 1 0 0 1 1-1zm1 2v10h6V2zm3 11a1 1 0 1 0 0 2 1 1 0 0 0 0-2z"/></svg>
        07700 900352
      </li>
      <li>
        <svg viewBox="0 0 16 16" aria-hidden="true"><path d="M4 1h8v4H4zM1 6h14v7h-3v2H4v-2H1zm4 5v3h6v-3z"/></svg>
        01632 960527
      </li>
      <li>
        <svg viewBox="0 0 16 16" aria-hidden="true"><path d="M1 3h14v1L8 9 1 4zm0 3l7 5 7-5v7H1z"/></svg>
        Harriet@plavex.co.uk
      </li>
    </ul>

    <div class="address">
      Brackwell House, Partridge Way<br>
      Norwich QB9 3KX<br>
      <span class="web">www.plavex.co.uk</span>
    </div>
  </section>

  <section class="card card-back">
    <div class="back-brand">
      <span class="brand-mark"></span>
      <span class="brand-name">Plavex</span>
    </div>
    <div class="back-web">www.plavex.co.uk</div>
  </section>
</div>
</body>
</html>
```